Verlindo Magician

I want the business card for my business to give to people who watch that later I will be employed to show magic here is my website http://www.verlindoillusions.example/I want the interesting design , i am very opened for formal and informal, I watch a lot of design so don't stick to the common shape and form but i hope it can also be produced the thing to write on will be the same as in picture that i will upload , i also will upload the logo for you that so can be easy to useDenis CostilleMagicianMAGICIAN VERLINDO 17 rue des Tilleuls - 25000 BESANÇON contact@verlindoillusions.example tel. 0381 946 157 tel. 0674 219 503

```html
<!DOCTYPE html>
<html lang="en">
<head>
<meta charset="utf-8">
<title>Verlindo Magician – Business Card</title>
<link rel="stylesheet" href="https://fonts.googleapis.com/css2?family=Jost:wght@400;500&display=swap">
<style>
  :root {
    --page: #e6e6e6;
    --ink: #0a0a0a;
    --paper: #ffffff;
    --red: #ec2227;
    --card-w: 826px;
    --card-h: 471px;
  }
  * { box-sizing: border-box; margin: 0; padding: 0; }
  html, body {
    width: 1125px; height: 1200px; overflow: hidden;
    background: var(--page);
    font-family: "Jost", "Futura", sans-serif;
  }
  .card {
    position: absolute; left: 150px;
    width: var(--card-w); height: var(--card-h);
    overflow: hidden;
    box-shadow: 0 2px 6px rgba(0,0,0,.25);
  }
  .card--front { top: 106px; background: var(--paper); }
  .card--back  { top: 639px; background: var(--red); }

  .wave { position: absolute; inset: 0; width: 100%; height: 100%; }

  .portrait {
    position: absolute;
    background: linear-gradient(180deg, #2a2a2a 0%, #050505 100%);
    border-radius: 40% 40% 18% 18% / 30% 30% 12% 12%;
  }
  .card--front .portrait { left: 113px; top: 42px; width: 175px; height: 185px; }
  .card--back .portrait  { left: 318px; top: 80px; width: 226px; height: 280px; }

  .brand {
    position: absolute; left: 100px; top: 250px; width: 200px;
    text-align: center;
    font-size: 33px; font-weight: 400; letter-spacing: 1px;
    color: var(--ink);
  }

  .details {
    position: absolute; right: 43px; top: 214px;
    text-align: right; color: var(--paper);
    font-size: 20px; line-height: 26px;
  }
  .details .name { color: var(--red); font-size: 30px; line-height: 34px; }
  .details .role { font-size: 21px; margin-bottom: 16px; }
  .details .line { display: flex; justify-content: flex-end; align-items: center; gap: 8px; }
  .details .line svg { width: 17px; height: 17px; flex: none; }
  .address {
    position: absolute; right: 43px; top: 421px;
    color: var(--paper); font-size: 20px;
  }

  .back-url {
    position: absolute; left: 0; right: 0; top: 414px;
    text-align: center; color: var(--paper);
    font-size: 19px; letter-spacing: 3px;
  }
</style>
</head>
<body>

<section class="card card--front">
  <svg class="wave" viewBox="0 0 800 456" preserveAspectRatio="none" aria-hidden="true">
    <path fill="var(--red)" d="M0,276 C120,330 230,372 330,334 C450,284 520,150 640,92 C700,66 760,60 800,64 L800,72 C760,70 700,78 640,104 C520,165 450,300 330,352 C230,392 120,352 0,300 Z"/>
    <path fill="var(--ink)" d="M0,306 C120,352 230,392 330,352 C450,300 520,168 640,108 C700,82 760,74 800,78 L800,84 C760,82 700,90 640,116 C520,176 450,310 330,360 C230,400 120,362 0,314 Z"/>
    <path fill="var(--ink)" d="M0,318 C120,362 230,404 330,368 C450,322 520,178 640,122 C700,97 760,90 800,97 L800,456 L0,456 Z"/>
  </svg>

  <div class="portrait" role="img" aria-label="Black ink illustration of the magician in a dark jacket holding a playing card"></div>
  <div class="brand">VERLINDO</div>

  <div class="details">
    <div class="name">Marc Ravoulet</div>
    <div class="role">Magician</div>
    <div class="line">0381 946 157
      <svg viewBox="0 0 24 24"><path fill="var(--red)" d="M6.6 10.8a15 15 0 0 0 6.6 6.6l2.2-2.2a1 1 0 0 1 1-.25 11 11 0 0 0 3.6.6 1 1 0 0 1 1 1V20a1 1 0 0 1-1 1A17 17 0 0 1 3 4a1 1 0 0 1 1-1h3.5a1 1 0 0 1 1 1 11 11 0 0 0 .6 3.6 1 1 0 0 1-.25 1z"/></svg>
    </div>
    <div class="line">0674 219 503
      <svg viewBox="0 0 24 24"><path fill="var(--red)" d="M6.6 10.8a15 15 0 0 0 6.6 6.6l2.2-2.2a1 1 0 0 1 1-.25 11 11 0 0 0 3.6.6 1 1 0 0 1 1 1V20a1 1 0 0 1-1 1A17 17 0 0 1 3 4a1 1 0 0 1 1-1h3.5a1 1 0 0 1 1 1 11 11 0 0 0 .6 3.6 1 1 0 0 1-.25 1z"/></svg>
    </div>
    <div class="line">contact@verlindoillusions.example
      <svg viewBox="0 0 24 24"><rect x="2" y="5" width="20" height="14" fill="var(--red)"/><path d="M2 5l10 8 10-8" fill="none" stroke="var(--ink)" stroke-width="1.6"/></svg>
    </div>
    <div class="line">www.verlindoillusions.example
      <svg viewBox="0 0 24 24"><circle cx="12" cy="12" r="10" fill="var(--red)"/><path d="M2 12h20M12 2c3 3 3 17 0 20M12 2c-3 3-3 17 0 20" fill="none" stroke="var(--ink)" stroke-width="1.4"/></svg>
    </div>
  </div>
  <div class="address">MAGICIAN VERLINDO , 17 rue des Tilleuls - 25000 BESANÇON</div>
</section>

<section class="card card--back">
  <div class="portrait" role="img" aria-label="Black ink illustration of the magician in a dark jacket holding a playing card"></div>
  <div class="back-url">www.verlindoillusions.example</div>
</section>

</body>
</html>
```